Accounting firm needing business card / letterhead designed
Marcus L. Trenholm, CPA
marcus@veltrowledger.com
www.veltrowledger.com
842 E Alder Ave Ashbrook, MN 43827
419-562-0974

```html
<!DOCTYPE html>
<html lang="en">
<head>
<meta charset="utf-8">
<title>Veltrow Ledger – Business Card</title>
<link href="https://fonts.googleapis.com/css2?family=Roboto:wght@400;700&family=Roboto+Condensed:wght@700&display=swap" rel="stylesheet">
<style>
  :root {
    --backdrop: #c4c4c4;
    --navy: #252063;
    --lime: #8cc63f;
    --paper: #f4f4f4;
    --ink: #4a4a4a;
    --white: #ffffff;
  }
  * { margin: 0; padding: 0; box-sizing: border-box; }
  html, body { width: 1200px; height: 960px; overflow: hidden; }
  body {
    background: var(--backdrop);
    position: relative;
    font-family: "Roboto", Arial, sans-serif;
  }
  .card {
    position: absolute;
    width: 600px;
    height: 342px;
    border-radius: 18px;
    overflow: hidden;
  }
  .card-front {
    left: 322px; top: 108px;
    background: var(--navy);
  }
  .card-back {
    left: 320px; top: 493px;
    background: var(--paper);
  }
  .brand-name {
    position: absolute;
    font-family: "Roboto", Arial, sans-serif;
    font-weight: 700;
    text-transform: uppercase;
    letter-spacing: 4px;
    white-space: nowrap;
  }
  .card-front .brand-name {
    left: 0; right: 0; top: 128px;
    text-align: center;
    font-size: 50px;
    color: var(--white);
  }
  .card-back .brand-name {
    right: 34px; top: 42px;
    font-size: 40px;
    color: var(--navy);
  }
  .front-web {
    position: absolute;
    left: 0; right: 0; top: 280px;
    text-align: center;
    color: var(--white);
    font-size: 14px;
    letter-spacing: 6.5px;
  }
  .name-accent {
    position: absolute;
    left: 0; top: 180px;
    width: 22px; height: 20px;
  }
  .person-name {
    position: absolute;
    left: 30px; top: 176px;
    font-family: "Roboto Condensed", Arial, sans-serif;
    font-weight: 700;
    font-size: 21px;
    color: var(--navy);
  }
  .address {
    position: absolute;
    left: 31px; top: 212px;
    font-size: 14px;
    font-style: normal;
    line-height: 19px;
    color: var(--ink);
  }
  .contacts {
    position: absolute;
    left: 31px; top: 259px;
    list-style: none;
    font-size: 14px;
    line-height: 19.5px;
    color: var(--ink);
  }
  .contacts li { display: flex; align-items: center; gap: 8px; }
  .contacts svg { width: 13px; height: 13px; fill: var(--navy); flex: none; }
</style>
</head>
<body>

<section class="card card-front">
  <div class="brand-name">Veltrow Ledger</div>
  <div class="front-web">www.veltrowledger.com</div>
</section>

<section class="card card-back">
  <div class="brand-name">Veltrow Ledger</div>

  <svg class="name-accent" viewBox="0 0 22 20" aria-hidden="true">
    <polygon points="0,0 16,0 11,20 0,20" fill="var(--navy)"/>
    <polygon points="18,0 22,0 17,20 13,20" fill="var(--lime)"/>
  </svg>
  <div class="person-name">Marcus L. Trenholm, CPA</div>

  <address class="address">
    842 E Alder Ave<br>
    Ashbrook, MN 43827
  </address>

  <ul class="contacts">
    <li>
      <svg viewBox="0 0 24 24"><path d="M6.6 10.8a15.1 15.1 0 0 0 6.6 6.6l2.2-2.2a1 1 0 0 1 1-.25 11.4 11.4 0 0 0 3.6.57 1 1 0 0 1 1 1V20a1 1 0 0 1-1 1A17 17 0 0 1 3 4a1 1 0 0 1 1-1h3.5a1 1 0 0 1 1 1c0 1.25.2 2.45.57 3.57a1 1 0 0 1-.25 1z"/></svg>
      419-562-0974
    </li>
    <li>
      <svg viewBox="0 0 24 24"><path d="M2 5h20v14H2z"/><path d="M2 6.5l10 7.5 10-7.5V5H2z" fill="var(--paper)"/><path d="M2 5h20L12 12.5z"/></svg>
      marcus@veltrowledger.com
    </li>
    <li>
      <svg viewBox="0 0 24 24"><circle cx="12" cy="12" r="10"/><path d="M12 2v20M2 12h20M5 6.5h14M5 17.5h14" stroke="var(--paper)" stroke-width="1.5" fill="none"/></svg>
      www.veltrowledger.com
    </li>
  </ul>
</section>

</body>
</html>
```